need corporate, modern business card created for Consulting Company

I need a slick business card using elements from my website, as well as, integrating my pixelforge-created logo (see files).

The business card needs to be:
1. Corporate and modern
2. Clean and professional

I've included a PSD with the logo/icon that you can use to create it. Feel free to try a metallic finish on the logo, make it bigger/small, underlay it. Whatever you need to do to make my card stand out.

Try a black background, or white background or gray.

The idea is for my card to be memorable as well as professional and corporate.

Target Market(s)

Corporate business in the US and Canada.

Industry/Entity Type

Business

Contact Information for Business Card

Commerce Advancing Methods
Martin Coles, Senior Partner
office: 1 877 555 0143
mobile: 1 519 555 0172
website: http://www.brightvale.example

Requirements
Must have
• Card-related information
• corporate, yet modern
• clean and professional
• incorporate the icon only
• must have an editable form when complete!
Nice to have
• metallic icon might be cool
• try it with white or black

```html
<!DOCTYPE html>
<html lang="en">
<head>
<meta charset="utf-8">
<title>Brightvale business card</title>
<link rel="stylesheet" href="https://fonts.googleapis.com/css2?family=Arimo:wght@400;700&display=swap">
<style>
  :root {
    --page: #d9d6d1;
    --card: #ffffff;
    --card-shade: #eef0f3;
    --blue: #3d8fd6;
    --blue-light: #6cb3e6;
    --blue-deep: #2f78c2;
    --ink: #2b2b2b;
    --swoosh: #1e1e1e;
  }
  * { margin: 0; padding: 0; box-sizing: border-box; }
  html, body { width: 1200px; height: 885px; overflow: hidden; }
  body {
    background: var(--page);
    font-family: "Arimo", Arial, sans-serif;
    color: var(--ink);
    position: relative;
  }
  .card {
    position: absolute;
    top: 291px;
    width: 530px;
    height: 303px;
    background: var(--card);
    border-radius: 4px;
    box-shadow: 0 8px 22px rgba(0,0,0,.22);
    overflow: hidden;
  }
  .card--front { left: 50px; }
  .card--back {
    left: 620px;
    background: linear-gradient(135deg, var(--card) 0%, var(--card-shade) 100%);
  }

  /* front */
  .front-band { position: absolute; inset: 0; }
  .brand {
    position: absolute;
    display: flex;
    align-items: center;
    gap: 10px;
    color: var(--blue);
    font-weight: 700;
  }
  .brand__mark { background: var(--blue); border-radius: 4px; }
  .card--front .brand { left: 34px; top: 30px; font-size: 40px; letter-spacing: -1px; }
  .card--front .brand__mark { width: 26px; height: 26px; }

  .contact {
    position: absolute;
    right: 30px;
    top: 84px;
    text-align: right;
    font-size: 13px;
    line-height: 19px;
  }
  .contact__address { margin-bottom: 10px; }
  .contact__row {
    display: flex;
    justify-content: flex-end;
    align-items: center;
    gap: 8px;
  }
  .contact__icon { width: 15px; height: 15px; flex: none; }

  .holder {
    position: absolute;
    left: 34px;
    bottom: 22px;
    color: #fff;
  }
  .holder__name { font-size: 24px; font-weight: 700; }
  .holder__title { font-size: 16px; margin-top: 2px; color: #e6f1fb; }

  /* back */
  .card--back .brand {
    left: 50%;
    top: 50%;
    transform: translate(-50%, -50%);
    font-size: 58px;
    letter-spacing: -1.5px;
    gap: 14px;
  }
  .card--back .brand__mark { width: 36px; height: 36px; }
</style>
</head>
<body>

<section class="card card--front" aria-label="Card front">
  <svg class="front-band" viewBox="0 0 530 303" width="530" height="303" aria-hidden="true">
    <defs>
      <linearGradient id="bandFill" x1="0" y1="0" x2="1" y2="1">
        <stop offset="0" stop-color="#3a86cf"/>
        <stop offset="0.6" stop-color="#5aa6e0"/>
        <stop offset="1" stop-color="#3d8fd6"/>
      </linearGradient>
    </defs>
    <path d="M0 140 C 120 200, 320 245, 530 250 L530 303 L0 303 Z" fill="url(#bandFill)"/>
    <path d="M0 140 C 120 200, 320 245, 530 250 L530 245 C 320 239, 125 190, 0 128 Z" fill="var(--swoosh)"/>
  </svg>

  <div class="brand">
    <span class="brand__mark"></span>
    <span class="brand__name">brightvale</span>
  </div>

  <div class="contact">
    <div class="contact__address">
      48 Harbour Lane West, Suite 1200<br>
      Kingston, Ontario, K7L 2P4
    </div>
    <div class="contact__row">
      <span>1 877 555 0143</span>
      <svg class="contact__icon" viewBox="0 0 16 16" aria-label="Office phone"><rect width="16" height="16" rx="2" fill="var(--blue)"/><path d="M5 3.5l2 2-1 1.2c.6 1.4 1.6 2.4 3 3l1.2-1 2 2-1.3 1.6C7.6 12 4 8.4 3.7 4.8z" fill="#fff"/></svg>
    </div>
    <div class="contact__row">
      <span>1 519 555 0172</span>
      <svg class="contact__icon" viewBox="0 0 16 16" aria-label="Mobile phone"><rect width="16" height="16" rx="2" fill="var(--blue)"/><rect x="5.5" y="3" width="5" height="10" rx="1" fill="#fff"/><rect x="6.5" y="4.5" width="3" height="6" fill="var(--blue)"/></svg>
    </div>
    <div class="contact__row">
      <span>info@brightvale.example</span>
      <svg class="contact__icon" viewBox="0 0 16 16" aria-label="Email"><rect width="16" height="16" rx="2" fill="var(--blue)"/><rect x="3" y="4.5" width="10" height="7" fill="#fff"/><path d="M3 4.5l5 4 5-4" fill="none" stroke="var(--blue)" stroke-width="1"/></svg>
    </div>
    <div class="contact__row">
      <span>www.brightvale.example</span>
      <svg class="contact__icon" viewBox="0 0 16 16" aria-label="Website"><rect width="16" height="16" rx="2" fill="var(--blue)"/><circle cx="8" cy="8" r="4.5" fill="none" stroke="#fff" stroke-width="1.2"/><path d="M3.5 8h9M8 3.5c-2 2.5-2 6.5 0 9M8 3.5c2 2.5 2 6.5 0 9" fill="none" stroke="#fff" stroke-width="1"/></svg>
    </div>
  </div>

  <div class="holder">
    <div class="holder__name">Martin Coles</div>
    <div class="holder__title">Senior Partner</div>
  </div>
</section>

<section class="card card--back" aria-label="Card back">
  <div class="brand">
    <span class="brand__mark"></span>
    <span class="brand__name">brightvale</span>
  </div>
</section>

</body>
</html>
```